Birchline Septic Solutions

Would like to see some single sided ones but would also like to see some double sided with one sided only being the logo. Owners name is Colin Vandro. Phone number is 555-214-0387
Services are pumping, inspections, installs, and repairs

Contact Information for Business Card

555-241-0387 Colin Vandro Alder Falls, OH

```html
<!DOCTYPE html>
<html lang="en">
<head>
<meta charset="utf-8">
<title>Birchline Septic Solutions – Business Card</title>
<link rel="stylesheet" href="https://fonts.googleapis.com/css2?family=Open+Sans:wght@400;600;700&display=swap">
<style>
  :root {
    --stage: #232323;
    --card: #1f2022;
    --card-edge: #2a2b2e;
    --teal: #22b8b0;
    --white: #ffffff;
    --muted: #e8e8e8;
  }
  * { box-sizing: border-box; margin: 0; padding: 0; }
  html, body {
    width: 1200px; height: 779px; overflow: hidden;
    background: var(--stage);
    font-family: "Open Sans", Arial, sans-serif;
  }
  .stage {
    position: relative; width: 1200px; height: 779px;
    display: flex; justify-content: center; align-items: center; gap: 80px;
  }
  .card {
    position: relative; width: 300px; height: 525px;
    background: var(--card); border-radius: 18px;
    box-shadow: 0 18px 40px rgba(0,0,0,.55);
    overflow: hidden;
  }
  /* back side */
  .card-back .pattern {
    position: absolute; inset: 0;
    background: linear-gradient(135deg, #5a5a5c 0%, #2c2d30 35%, #17181a 70%, #121315 100%);
  }
  .card-back .back-mark {
    position: absolute; top: 38px; right: 30px;
    display: flex; align-items: center; gap: 8px;
    color: var(--white); font-weight: 700; font-size: 13px; letter-spacing: .5px;
  }
  .mark-dot { width: 10px; height: 10px; border-radius: 50%; background: var(--teal); }
  /* front side */
  .front-mark {
    position: absolute; top: 70px; left: 0; right: 0;
    text-align: center; color: var(--white);
    font-weight: 700; font-size: 22px; line-height: 1.15; letter-spacing: 1px;
    text-transform: uppercase;
  }
  .identity { position: absolute; top: 238px; left: 0; right: 0; text-align: center; }
  .name { font-size: 24px; font-weight: 700; color: var(--white); line-height: 1.1; }
  .name .first { color: var(--teal); }
  .location { font-size: 13px; color: var(--muted); margin-top: 2px; }
  .dots { position: absolute; left: 0; width: 300px; height: 20px; }
  .phone-icon { position: absolute; top: 286px; left: 136px; }
  .phone {
    position: absolute; top: 318px; left: 0; right: 0; text-align: center;
    color: var(--white); font-size: 19px; letter-spacing: .5px;
  }
  .services-pill {
    position: absolute; top: 352px; left: 50%; transform: translateX(-50%);
    background: var(--teal); color: var(--white);
    font-size: 12px; font-weight: 600; letter-spacing: .5px;
    padding: 3px 18px; border-radius: 50%;
  }
  .services-arrow { position: absolute; top: 374px; left: 145px; }
  .services-list {
    position: absolute; top: 390px; left: 0; right: 0; list-style: none;
    text-align: center; color: var(--muted); font-size: 13.5px; line-height: 1.35;
  }
</style>
</head>
<body>
<main class="stage">
  <section class="card card-back" aria-label="Card back">
    <div class="pattern" role="img" aria-label="Repeating mountain-and-pine pattern with a silver foil sheen"></div>
    <div class="back-mark"><span class="mark-dot"></span>Birchline Septic Solutions</div>
  </section>

  <section class="card card-front" aria-label="Card front">
    <div class="front-mark">Birchline<br><span style="font-size:13px;letter-spacing:3px">Septic Solutions</span></div>

    <div class="identity">
      <p class="name"><span class="first">Colin</span> Vandro</p>
      <p class="location">Alder Falls, OH</p>
    </div>

    <svg class="dots" style="top:296px" viewBox="0 0 300 20" aria-hidden="true">
      <g fill="var(--teal)">
        <circle cx="10" cy="10" r="2"/><circle cx="26" cy="10" r="2.6"/><circle cx="44" cy="10" r="3.2"/><circle cx="64" cy="10" r="3.8"/><circle cx="86" cy="10" r="4.4"/><circle cx="110" cy="10" r="5"/>
        <circle cx="190" cy="10" r="5"/><circle cx="214" cy="10" r="4.4"/><circle cx="236" cy="10" r="3.8"/><circle cx="256" cy="10" r="3.2"/><circle cx="274" cy="10" r="2.6"/><circle cx="290" cy="10" r="2"/>
      </g>
    </svg>
    <svg class="phone-icon" width="28" height="32" viewBox="0 0 28 32" aria-hidden="true">
      <circle cx="14" cy="13" r="12" fill="var(--teal)"/>
      <path d="M9 8c1-1 2 0 3 2s-1 2 0 3 1 2 3 3 2-1 3 0 1 2 0 3c-3 2-10-4-9-11z" fill="var(--white)"/>
      <path d="M10 26h8l-4 5z" fill="var(--teal)"/>
    </svg>
    <p class="phone">555-241-0387</p>

    <svg class="dots" style="top:355px" viewBox="0 0 300 20" aria-hidden="true">
      <g fill="var(--teal)">
        <circle cx="12" cy="10" r="2"/><circle cx="28" cy="10" r="2.6"/><circle cx="46" cy="10" r="3.2"/><circle cx="66" cy="10" r="3.8"/><circle cx="86" cy="10" r="4.4"/>
        <circle cx="214" cy="10" r="4.4"/><circle cx="234" cy="10" r="3.8"/><circle cx="254" cy="10" r="3.2"/><circle cx="272" cy="10" r="2.6"/><circle cx="288" cy="10" r="2"/>
      </g>
    </svg>
    <span class="services-pill">SERVICES</span>
    <svg class="services-arrow" width="10" height="10" viewBox="0 0 10 10" aria-hidden="true"><path d="M0 0h10L5 8z" fill="var(--teal)"/></svg>
    <ul class="services-list">
      <li>Installs</li>
      <li>Pumping</li>
      <li>Inspections</li>
      <li>And Repairs</li>
    </ul>
  </section>
</main>
</body>
</html>
```